New Organic Skin Care Line Needs to Design a Product Label

***THE WINNER OF THIS PROJECT WILL MOST LIKELY BECOME THE EXCLUSIVE DESIGNER FOR OUR OTHER PRODUCT LABELS***

We need a label design for a new organic skin care product line called "Maple Dew Gala." This specific product is a 100% pure organic coconut oil. It's used for skin hydration, protection, and makeup removal.

Info to include on front label:

1. Logo: Maple Dew Gala (attached)
2. Product Name: Pure Coconut Oil (emphasize "organic" somewhere)
3. Slogan: Hydrate your skin and hair.
4. Size: 8 FL OZ 236mL

Attached is:

1. The brand logo "Maple Dew Gala" with a white background.
2. An image of the bottle we will use.
3. An image of the bottle with lines to show the size and placement of the label.
4. The brand logo "Maple Dew Gala" with a black background. (photoshop file)

What we need:

A simple mock up of the front side of the label on the bottle. We first want to know what it will look like on the bottle given the size and dimensions.

- We would like one label with a white background (including the logo with a white background).
- We would like a second label with a black background (including the logo with a black background, just need to make the black font white instead of black).

We can get a great idea of what to expect from the front side of the label so we will complete the back side once we identify a winner.
Updates

Apologies, but we are now using a different bottle. The previous one is now discontinued. Please view the two most recent images uploaded. One is an image of the new bottle by itself. The other is an image of that bottle with instructions. Please use your most recent designs on the new bottle. Feel free to make any modifications you see fit to compliment the new bottle shape. Added Friday, March 18, 2016

Reason: We are still working with the label company to finalize the size. Once the size is confirmed we will have to tweak labels based on finalized measurements.

Target Market(s)

Women, 18-70

Industry/Entity Type

Skin Care Product

Font styles to use
Decorative
Script

Requirements
Must have
• -"shabby sheek" and "cute" theme
• -soft organic feel
• -the ingredients are organic, pure, and natural. That should be an essence of the label.

```html
<!DOCTYPE html>
<html lang="en">
<head>
<meta charset="utf-8">
<title>Maple Dew Gala – Pure Coconut Oil Front Label</title>
<link rel="stylesheet" href="https://fonts.googleapis.com/css2?family=Cinzel:wght@400;600&family=Poiret+One&family=Arimo&display=swap">
<style>
  :root {
    --canvas-bg: #ffffff;
    --label-black: #050505;
    --band-silver-light: #e6e6e6;
    --band-silver-dark: #a9a9a9;
    --text-white: #ffffff;
    --organic-green: #a9c73a;
    --coconut-brown: #9a7650;
    --coconut-cream: #f3efe6;
    --leaf-green: #4f7a3a;
  }
  html, body {
    margin: 0;
    padding: 0;
    width: 716px;
    height: 1200px;
    overflow: hidden;
    background: var(--canvas-bg);
  }
  .canvas {
    position: relative;
    width: 716px;
    height: 1200px;
  }
  .label {
    position: absolute;
    left: 70px;
    top: 330px;
    width: 575px;
    height: 540px;
  }
  .label-shape {
    position: absolute;
    inset: 0;
    width: 575px;
    height: 540px;
  }
  .label-text {
    position: absolute;
    left: 0;
    width: 575px;
    margin: 0;
    text-align: center;
    color: var(--text-white);
    line-height: 1;
  }
  .brand-name {
    top: 163px;
    font-family: "Cinzel", serif;
    font-weight: 400;
    font-size: 21px;
    letter-spacing: 0.22em;
  }
  .ingredient-illustration {
    position: absolute;
    left: 197px;
    top: 228px;
    width: 180px;
    height: 100px;
    border-radius: 50%;
    background: radial-gradient(ellipse at 40% 50%, var(--coconut-cream) 0%, var(--coconut-brown) 55%, var(--leaf-green) 100%);
  }
  .product-name {
    top: 344px;
    font-family: "Cinzel", serif;
    font-weight: 600;
    font-size: 36px;
    letter-spacing: 0.01em;
  }
  .slogan {
    top: 393px;
    font-family: "Cinzel", serif;
    font-weight: 600;
    font-size: 15px;
    letter-spacing: 0.02em;
  }
  .organic-row {
    position: absolute;
    left: 0;
    top: 446px;
    width: 575px;
    display: flex;
    justify-content: center;
    align-items: center;
    gap: 12px;
  }
  .organic-flourish {
    width: 125px;
    height: 14px;
  }
  .organic-word {
    font-family: "Poiret One", sans-serif;
    font-size: 32px;
    color: var(--organic-green);
    letter-spacing: 0.02em;
    line-height: 1;
  }
  .volume {
    top: 510px;
    font-family: "Arimo", sans-serif;
    font-size: 19px;
    letter-spacing: 0.06em;
  }
</style>
</head>
<body>
<main class="canvas">
  <section class="label" aria-label="Maple Dew Gala Pure Coconut Oil front label">
    <svg class="label-shape" viewBox="0 0 575 540" aria-hidden="true">
      <defs>
        <clipPath id="label-outline">
          <path d="M100,0 L475,0 C530,60 575,150 575,270 C575,390 540,470 475,540 L100,540 C35,470 0,390 0,270 C0,150 45,60 100,0 Z"/>
        </clipPath>
        <linearGradient id="silver-band" x1="0" y1="0" x2="1" y2="0">
          <stop offset="0" stop-color="var(--band-silver-dark)"/>
          <stop offset="0.5" stop-color="var(--band-silver-light)"/>
          <stop offset="1" stop-color="var(--band-silver-dark)"/>
        </linearGradient>
      </defs>
      <g clip-path="url(#label-outline)">
        <rect x="0" y="0" width="575" height="540" fill="var(--label-black)"/>
        <rect x="0" y="260" width="575" height="38" fill="url(#silver-band)"/>
      </g>
    </svg>

    <p class="label-text brand-name">MAPLE DEW GALA</p>

    <div class="ingredient-illustration" role="img" aria-label="Illustration of a halved coconut and whole coconut on green leaves"></div>

    <h1 class="label-text product-name">PURE COCONUT OIL</h1>
    <p class="label-text slogan">HYDRATE YOUR SKIN AND HAIR</p>

    <div class="organic-row">
      <svg class="organic-flourish" viewBox="0 0 125 14" aria-hidden="true">
        <path d="M2,8 C20,4 40,10 62,7 C85,4 105,9 123,7" fill="none" stroke="var(--text-white)" stroke-width="2.4" stroke-linecap="round"/>
      </svg>
      <span class="organic-word">ORGANIC</span>
      <svg class="organic-flourish" viewBox="0 0 125 14" aria-hidden="true">
        <path d="M2,7 C20,9 40,4 63,7 C85,10 105,5 123,8" fill="none" stroke="var(--text-white)" stroke-width="2.4" stroke-linecap="round"/>
      </svg>
    </div>

    <p class="label-text volume">236 ML</p>
  </section>
</main>
</body>
</html>
```